Design a New Business Card for Our Company

We are looking for fresh, unique, and a modern business card that reflects our roots as digital marketing agency focused on SEM.

Industry/Entity Type

Marketing

Contact Information for Business Card

looking for very unique out of the box designs. clean and modern that compliments our logo

Requirements
Must have
• colors should match our logo
• Front should have name, address, email, and phone/fax of the person, phone/fax are the same number
• back should have our url

```html
<!DOCTYPE html>
<html lang="en">
<head>
<meta charset="utf-8">
<title>Brightpath Solutions — Business Card</title>
<link rel="stylesheet" href="https://fonts.googleapis.com/css2?family=Open+Sans:wght@300;400;600;700&display=swap">
<style>
  :root {
    --backdrop: #2b2b2d;
    --card-dark: #3a3b3e;
    --card-light: #ffffff;
    --card-light-shade: #e9ebee;
    --brand-blue: #3d7fc6;
    --text-light: #e6e6e6;
    --text-muted: #a9abb0;
  }
  * { box-sizing: border-box; margin: 0; padding: 0; }
  html, body {
    width: 1200px; height: 997px; overflow: hidden;
    background: var(--backdrop);
    font-family: "Open Sans", Arial, sans-serif;
  }
  .canvas { position: relative; width: 1200px; height: 997px; }

  .card {
    position: absolute; width: 520px; height: 300px;
    border-radius: 18px; overflow: hidden;
    box-shadow: 0 14px 30px rgba(0,0,0,0.45);
  }

  .brand {
    position: absolute; left: 50%; transform: translateX(-50%);
    display: flex; align-items: center; gap: 12px;
    white-space: nowrap;
  }
  .brand-mark {
    flex: 0 0 28px; width: 28px; height: 28px;
    border-radius: 50%; background: var(--brand-blue);
  }
  .brand-name { font-weight: 600; font-size: 30px; letter-spacing: -0.5px; line-height: 1; }

  /* Front card */
  .card-front { left: 60px; top: 150px; background: var(--card-dark); }
  .front-top {
    position: absolute; left: 0; top: 0; width: 100%; height: 168px;
    background: linear-gradient(180deg, var(--card-light) 0%, var(--card-light) 60%, var(--card-light-shade) 100%);
  }
  .front-divider { position: absolute; left: 0; top: 158px; width: 520px; height: 22px; }
  .card-front .brand { top: 66px; }
  .card-front .brand-name { color: var(--brand-blue); }

  .person { position: absolute; left: 34px; top: 190px; }
  .person-name { font-size: 20px; font-weight: 400; color: var(--brand-blue); line-height: 1.1; }
  .person-title { font-size: 11px; color: var(--text-muted); margin-top: 2px; }
  .contact-list { list-style: none; margin-top: 10px; }
  .contact-list li {
    display: flex; align-items: center; gap: 12px;
    font-size: 13px; color: var(--text-light); margin-bottom: 6px;
  }
  .contact-list svg { width: 14px; height: 14px; fill: var(--brand-blue); flex: 0 0 14px; }

  .office { position: absolute; right: 30px; top: 192px; text-align: right; }
  .office-name { font-size: 13px; color: var(--brand-blue); }
  .office-address { font-size: 10px; color: var(--text-muted); line-height: 1.4; }

  /* Back card */
  .card-back { left: 620px; top: 430px; background: var(--card-dark); }
  .card-back .brand { top: 30px; }
  .card-back .brand-name { color: var(--text-light); }
  .sem-artwork {
    position: absolute; left: 70px; top: 84px; width: 380px; height: 168px;
    border-radius: 6px;
    background: radial-gradient(ellipse at 50% 50%, #8a8c88 0%, #5f615f 55%, #45474a 100%);
  }
  .site-url {
    position: absolute; left: 0; right: 0; bottom: 16px;
    text-align: center; font-size: 13px; letter-spacing: 0.5px;
    color: var(--brand-blue);
  }
</style>
</head>
<body>
<main class="canvas">

  <section class="card card-front" aria-label="Business card front">
    <div class="front-top"></div>
    <svg class="front-divider" viewBox="0 0 520 22" aria-hidden="true">
      <polyline points="0,10 24,10 32,18 40,10 520,10" fill="none" stroke="var(--brand-blue)" stroke-width="2.5"/>
    </svg>

    <div class="brand">
      <span class="brand-mark"></span>
      <span class="brand-name">Brightpath Solutions</span>
    </div>

    <div class="person">
      <p class="person-name">Marcus Lind</p>
      <p class="person-title">Chairman</p>
      <ul class="contact-list">
        <li>
          <svg viewBox="0 0 24 24" aria-hidden="true"><path d="M6.6 10.8a15.1 15.1 0 0 0 6.6 6.6l2.2-2.2a1 1 0 0 1 1-.25 11.4 11.4 0 0 0 3.6.6 1 1 0 0 1 1 1V20a1 1 0 0 1-1 1A17 17 0 0 1 3 4a1 1 0 0 1 1-1h3.5a1 1 0 0 1 1 1c0 1.25.2 2.45.6 3.6a1 1 0 0 1-.25 1z"/></svg>
          +46 700 412 580
        </li>
        <li>
          <svg viewBox="0 0 24 24" aria-hidden="true"><path d="M2 5h20v14H2z"/><path d="M3 6l9 7 9-7" fill="none" stroke="var(--card-dark)" stroke-width="1.6"/></svg>
          hello@brightpath.example
        </li>
      </ul>
    </div>

    <div class="office">
      <p class="office-name">Brightpath Solutions</p>
      <p class="office-address">No.2400, Harbor Road<br>Ontario, Canada</p>
    </div>
  </section>

  <section class="card card-back" aria-label="Business card back">
    <div class="brand">
      <span class="brand-mark"></span>
      <span class="brand-name">Brightpath Solutions</span>
    </div>
    <div class="sem-artwork" role="img" aria-label="Large letters SEM filled with a word cloud of marketing terms such as keywords, analysis and pay per click, with a magnifying glass"></div>
    <p class="site-url">www.brightpath.example</p>
  </section>

</main>
</body>
</html>
```